Redo our website for our Robotics company

We sell robotic equipment to the restaurant industry. Our current robot, is a cooking robot that cooks up to 15 lbs of food. We will provide a prior website as well as brand guidelines. We plan on using wordpress and take advantage of wordpress's visual (no code) editor.

Current website - https://kelvatrix88.com/ (please note we are only selling Tammo now and no longer selling Plavo+

We want someone to take our existing content and design the website as well as layout our content we provide. Here's a suggested site layout:

✅ KelvaTrix88 Website Wireframe / Site Map
1. Home

Purpose: Introduce Tammo, establish credibility, drive demo requests.

Sections:

Hero Section

Headline: “Meet Tammo — Your New Robotic Chef for High-Volume, Consistent Cooking.”

Sub-headline: Increase throughput. Reduce labor. Deliver perfect food every time.

CTA: Request a Demo + Watch Tammo Cook

Visual: Video loop or hero animation of Tammo in action.

How Tammo Works (3-4 steps)

Step cards: Load Ingredients → Select Recipe → Tammo Cooks → Serve

Icons and short explanations.

Key Benefits

Labor savings

Zero inconsistency

24/7 uptime

Throughput increases (30–50% faster)

Health & safety compliance

Who It’s For

QSR restaurants

Fast casual

Catering/commissaries

Ghost kitchens

Case Studies / Testimonials

Logo bar + quotes

“Tammo helped us reduce cooking times by 40%.”

Video Section

“Watch Tammo cook a full batch from start to finish.”

CTA Section

Big banner: Book a Demo

2. Product: “Meet Tammo”

Purpose: Deep dive into hardware, software, safety, reliability.

Sections:

Overview

What Tammo is

What tasks it automates

Where it fits in a kitchen

Hardware Features

High-temperature cooking chamber

Precision sensors

Automated stirring

Automated dispensing

Safety mechanisms (locking lids, auto-shutoff)

Software & AI

Recipe automation

IoT dashboard

Remote monitoring

Predictive maintenance

Specs Table

Dimensions

Power requirements

Capacity (lbs per batch)

Safety certifications

Gallery

Close-ups, installation photos, process shots

CTA: Request a Demo

3. Solutions

Purpose: Show that Tammo solves real operational problems.

Sub-pages or sections:

For Quick-Service Restaurants

Reduce labor cost

Speed up peak-hour demand

For Catering & Commissaries

Large-batch consistency

Automate repetitive cooking tasks

For High-Growth Chains

Replicable quality across multiple locations

Centralized recipe control

Each solution page includes:

A problem statement

How Tammo solves it

Metrics / KPIs

Relevant testimonial

CTA

4. ROI / Economics

Purpose: Sell the financial story clearly.

Sections:

Savings Calculator

Labor hours saved

Cost savings

Throughput increases

Food waste reduction

Before & After Comparison

Traditional kitchen vs. robotic kitchen

Sample ROI

“Payback in as little as 3–6 months.”

Download Full ROI Report (PDF)

5. Case Studies

Purpose: Social proof + real results.

Structure for each case study:

Customer background

Problem

Implementation

KPIs achieved

Labor savings

Consistency improvements

Cooking speed

Quote + photos/video

6. Pricing

Purpose: Start a commercial conversation.

Include:

Subscription model (monthly / annual)

Hardware leasing or purchase options

Installation + training

Support level

CTA to book a sales call

7. About

Purpose: Build trust.

Sections:

Mission statement

Founding team

Advisors/partners

“Why we built Tammo”

8. Resources

Purpose: SEO + education.

Subpages:

Blog (e.g., “The Future of Automated Kitchens”)

Whitepapers

Technical documentation

Product videos

9. Contact

General inquiry form

Sales contact

Support portal

Careers

```html
<!DOCTYPE html>
<html lang="en">
<head>
<meta charset="utf-8">
<title>KelvaTrix88 — Meet Tammo</title>
<link href="https://fonts.googleapis.com/css2?family=Montserrat:wght@500;600;700;800&family=Lato:wght@400;700&display=swap" rel="stylesheet">
<style>
:root{
  --red:#ee3b24;
  --red-2:#f7572a;
  --ink:#1c1c1c;
  --muted:#555;
  --navy:#0b2a5f;
  --navy-2:#0f3878;
  --blush:#fcefe8;
  --footer:#141414;
  --white:#fff;
}
*{margin:0;padding:0;box-sizing:border-box}
html,body{width:1200px;height:4637px;overflow:hidden}
body{position:relative;background:var(--white);font-family:'Lato',sans-serif;color:var(--ink)}
.abs{position:absolute}
.heading{font-family:'Montserrat',sans-serif;font-weight:800}
.tag{display:inline-block;background:var(--red);color:var(--white);transform:skewX(-14deg);padding:0 14px;border-radius:4px;margin-left:6px}
.tag span{display:inline-block;transform:skewX(14deg)}
.btn{display:inline-flex;align-items:center;justify-content:center;font-family:'Montserrat',sans-serif;font-weight:700;font-size:15px;color:var(--white);background:linear-gradient(90deg,var(--red),var(--red-2));transform:skewX(-14deg);border-radius:6px}
.btn span{transform:skewX(14deg)}
.btn.ghost{background:transparent;border:2px solid var(--red)}

/* header */
.site-header{left:0;top:0;width:1200px;height:86px;background:var(--white)}
.brand{left:108px;top:24px;font-family:'Montserrat',sans-serif;font-weight:800;font-size:32px;color:var(--red);letter-spacing:-.5px;display:flex;align-items:center;gap:8px}
.brand i{width:12px;height:12px;background:var(--red);display:block}
.nav{left:374px;top:32px;display:flex;gap:16px;font-size:15px;font-family:'Lato',sans-serif;color:#333}
.nav .active{color:var(--red)}
.contact-btn{left:962px;top:22px;width:120px;height:40px}

/* hero */
.hero{left:0;top:86px;width:1200px;height:600px;border-radius:0 0 70px 70px;overflow:hidden;background:linear-gradient(100deg,#141414 0%,#2a2a2a 45%,#4a4a4a 75%,#2b2b2b 100%)}
.hero h1{left:106px;top:138px;font-size:48px;line-height:52px;color:var(--white);width:800px}
.hero p{left:106px;top:312px;font-size:17px;color:#f1f1f1}
.hero .b1{left:118px;top:355px;width:170px;height:42px}
.hero .b2{left:306px;top:355px;width:196px;height:42px}

/* how it works */
.section-title{width:1200px;text-align:center;font-size:34px;color:var(--red)}
.steps-title{left:0;top:758px}
.step{width:240px;text-align:center}
.step .ring{width:108px;height:108px;border-radius:50%;border:2px dashed var(--red);margin:0 auto;display:flex;align-items:center;justify-content:center}
.step .dot{width:90px;height:90px;border-radius:50%;background:radial-gradient(circle at 40% 35%,var(--red-2),var(--red));display:flex;align-items:center;justify-content:center}
.step h3{font-family:'Montserrat',sans-serif;font-weight:600;font-size:17px;margin-top:22px}
.step p{font-size:14px;line-height:23px;color:var(--muted);margin-top:10px}

/* benefits */
.benefits{left:0;top:1162px;width:1200px;height:770px;background:radial-gradient(ellipse at 70% 20%,var(--navy-2),var(--navy) 60%)}
.benefits .section-title{top:96px;color:var(--white)}
.benefits .tag{background:var(--red)}
.b-item{color:var(--white)}
.b-item h4{font-family:'Montserrat',sans-serif;font-weight:700;font-size:17px}
.b-item p{font-size:15px;line-height:26px;margin-top:8px}
.b-left{text-align:right;width:300px}
.b-icon{width:86px;height:86px;border:2px solid var(--white);border-radius:50%;display:flex;align-items:center;justify-content:center}
.center-mark{font-family:'Montserrat',sans-serif;font-weight:800;font-size:34px;color:var(--white);width:400px;text-align:center}

/* quote banner */
.quote-banner{left:110px;top:2024px;width:977px;height:426px;border-radius:14px;background:linear-gradient(180deg,#3b3b3b,#252525 60%,#333);overflow:hidden}
.quote-banner h2{width:977px;text-align:center;top:120px;font-size:42px;line-height:54px;color:var(--white)}
.quote-banner .btn{left:402px;top:245px;width:190px;height:42px}

/* audience */
.audience-title{left:0;top:2555px}
.aud{width:234px;text-align:center}
.aud .photo{height:260px;border-radius:16px}
.aud h5{font-family:'Montserrat',sans-serif;font-weight:600;font-size:16px;margin-top:18px}

/* testimonials */
.testimonials{left:0;top:3017px;width:1200px;height:460px;background:var(--blush)}
.testimonials .section-title{top:88px}
.t-card{top:153px;width:312px;height:207px;background:var(--white);box-shadow:0 4px 14px rgba(0,0,0,.12);padding:18px 16px}
.t-head{display:flex;align-items:center;gap:16px}
.avatar{width:72px;height:72px;border-radius:50%;background:linear-gradient(135deg,#c9b3a6,#6b5a55)}
.t-name{font-family:'Montserrat',sans-serif;font-weight:600;font-size:15px}
.t-place{font-size:12px;color:#777;margin-top:8px;display:flex;align-items:center;gap:8px}
.t-place i{width:24px;height:12px;background:linear-gradient(180deg,#fff 33%,#2a4fa5 33% 66%,#d8262b 66%);display:block;border:1px solid #ddd}
.quote-mark{position:absolute;right:18px;top:14px;font-family:'Montserrat',sans-serif;font-weight:800;font-size:54px;color:#ddd;line-height:1}
.t-card p{font-size:14px;line-height:31px;color:#777;margin-top:16px}

/* video */
.video-title{left:0;top:3540px;width:1200px;text-align:center;font-size:34px;line-height:42px;color:var(--red)}
.video{left:110px;top:3652px;width:980px;height:460px;background:radial-gradient(circle at 55% 45%,#5a5e6e,#2a2c36 70%);clip-path:polygon(32px 0,100% 0,970px 460px,0 100%,0 60px);border-radius:20px}
.play{left:575px;top:3858px;width:50px;height:50px;border-radius:50%;background:var(--white);display:flex;align-items:center;justify-content:center}

/* footer */
.site-footer{left:0;top:4208px;width:1200px;height:429px;background:var(--footer);border-radius:70px 70px 0 0;color:var(--white)}
.f-col h6{font-family:'Montserrat',sans-serif;font-weight:600;font-size:21px}
.f-col ul{list-style:none;margin-top:16px}
.f-col li{font-size:14px;line-height:31px;display:flex;align-items:center;gap:12px}
.f-contact{display:flex;align-items:center;gap:14px;font-size:14px;margin-top:24px}
.f-contact .ic{width:34px;height:34px;border-radius:50%;background:var(--red);display:flex;align-items:center;justify-content:center}
.news p{font-size:14px;line-height:30px;margin-top:20px;color:#ddd}
.news .field{margin-top:12px;border-bottom:1px solid #bbb;width:272px;padding-bottom:8px;font-size:14px}
.subscribe{width:146px;height:48px;border-radius:26px;background:var(--red);display:flex;align-items:center;justify-content:center;font-family:'Montserrat',sans-serif;font-weight:600;font-size:16px;margin-top:30px;margin-left:8px}
.f-rule{left:97px;top:365px;width:1004px;height:1px;background:#777}
.copyright{left:0;top:388px;width:1200px;text-align:center;font-size:14px}
</style>
</head>
<body>

<header class="site-header abs">
  <div class="brand abs"><i></i>KelvaTrix88</div>
  <nav class="nav abs">
    <span class="active">Home</span><span>Product</span><span>Solutions</span><span>ROI</span><span>Case Studies</span><span>Pricing</span><span>About</span><span>Resources</span>
  </nav>
  <a class="btn contact-btn abs"><span>Contact Us</span></a>
</header>

<section class="hero abs" role="img" aria-label="Row of Tammo cooking robots in a commercial kitchen">
  <h1 class="heading abs">Meet Tammo — Your New Robotic Chef for High-Volume, Consistent Cooking.</h1>
  <p class="abs">Increase throughput. Reduce labor. Deliver perfect food every time.</p>
  <a class="btn b1 abs"><span>Request a Demo</span></a>
  <a class="btn ghost b2 abs"><span>Watch Tammo Cook</span></a>
</section>

<h2 class="section-title heading abs steps-title">How Tammo <span class="tag"><span>Works</span></span></h2>
<svg class="abs" style="left:196px;top:860px" width="800" height="110" viewBox="0 0 800 110" fill="none" stroke="#333" stroke-width="1.5" stroke-dasharray="2 4">
  <path d="M50 30 C110 -5 200 -5 240 30"/>
  <path d="M310 60 C360 90 470 90 500 60"/>
  <path d="M575 30 C630 -5 720 -5 760 30"/>
</svg>
<div class="step abs" style="left:76px;top:856px">
  <div class="ring"><div class="dot"><svg width="40" height="40" viewBox="0 0 40 40" fill="none" stroke="#fff" stroke-width="2.5"><path d="M6 20h28a14 14 0 0 1-28 0z"/><circle cx="15" cy="12" r="3"/><circle cx="25" cy="12" r="3"/></svg></div></div>
  <h3>Load Ingredients</h3><p>Lorem ipsum dolor sit amet, consectetur adipiscing elit, sed do eiusmod</p>
</div>
<div class="step abs" style="left:342px;top:856px">
  <div class="ring"><div class="dot"><svg width="40" height="40" viewBox="0 0 40 40" fill="none" stroke="#fff" stroke-width="2.5"><rect x="9" y="5" width="22" height="30" rx="2"/><path d="M14 14h12M14 20h12M14 26h8"/></svg></div></div>
  <h3>Select Recipe</h3><p>Lorem ipsum dolor sit amet, consectetur adipiscing elit, sed do eiusmod</p>
</div>
<div class="step abs" style="left:607px;top:856px">
  <div class="ring"><div class="dot"><svg width="40" height="40" viewBox="0 0 40 40" fill="none" stroke="#fff" stroke-width="2.5"><path d="M6 18h28v10a6 6 0 0 1-6 6H12a6 6 0 0 1-6-6z"/><path d="M2 18h4M34 18h4M14 12v-4M20 12v-6M26 12v-4"/></svg></div></div>
  <h3>Tammo Cooks</h3><p>Lorem ipsum dolor sit amet, consectetur adipiscing elit, sed do eiusmod</p>
</div>
<div class="step abs" style="left:871px;top:856px">
  <div class="ring"><div class="dot"><svg width="40" height="40" viewBox="0 0 40 40" fill="none" stroke="#fff" stroke-width="2.5"><path d="M7 28a13 13 0 0 1 26 0z"/><path d="M4 32h32M20 11v4"/></svg></div></div>
  <h3>Serve</h3><p>Lorem ipsum dolor sit amet, consectetur adipiscing elit, sed do eiusmod</p>
</div>

<section class="benefits abs">
  <h2 class="section-title heading abs">Key<span class="tag"><span>Benefits</span></span></h2>
  <svg class="abs" style="left:0;top:0" width="1200" height="770" fill="none">
    <path d="M729 195 A162 162 0 1 1 470 195" stroke="#fff" stroke-width="3"/>
    <g fill="var(--red)" stroke="#fff" stroke-width="2">
      <circle cx="470" cy="195" r="8"/><circle cx="729" cy="195" r="8"/>
      <circle cx="446" cy="360" r="8"/><circle cx="748" cy="360" r="8"/>
      <circle cx="599" cy="455" r="8"/>
    </g>
  </svg>
  <div class="center-mark abs" style="left:399px;top:270px">KelvaTrix88</div>

  <div class="b-item b-left abs" style="left:18px;top:152px"><h4>Zero inconsistency</h4><p>Lorem ipsum dolor sit amet,<br>labore et dolore magna aliqua.</p></div>
  <div class="b-icon abs" style="left:335px;top:157px"><svg width="44" height="44" viewBox="0 0 44 44" fill="none" stroke="#fff" stroke-width="2"><path d="M17 6h10M19 6v10L9 34a4 4 0 0 0 4 5h18a4 4 0 0 0 4-5L25 16V6"/><circle cx="20" cy="30" r="3"/></svg></div>

  <div class="b-item b-left abs" style="left:18px;top:308px"><h4>Health &amp; safety compliance</h4><p>Lorem ipsum dolor sit amet,<br>labore et dolore magna aliqua.</p></div>
  <div class="b-icon abs" style="left:331px;top:325px"><svg width="44" height="44" viewBox="0 0 44 44" fill="none" stroke="#fff" stroke-width="2"><path d="M22 8l10 4v9c0 7-5 11-10 13-5-2-10-6-10-13v-9z"/><path d="M17 21l4 4 7-7"/></svg></div>

  <div class="b-icon abs" style="left:781px;top:157px"><svg width="44" height="44" viewBox="0 0 44 44" fill="none" stroke="#fff" stroke-width="2"><circle cx="22" cy="14" r="7"/><path d="M9 38c0-8 6-13 13-13s13 5 13 13"/><circle cx="32" cy="32" r="5"/></svg></div>
  <div class="b-item abs" style="left:882px;top:155px"><h4>Labor savings</h4><p>Lorem ipsum dolor sit amet,<br>labore et dolore magna aliqua.</p></div>

  <div class="b-icon abs" style="left:781px;top:325px"><svg width="44" height="44" viewBox="0 0 44 44" fill="none" stroke="#fff" stroke-width="2"><circle cx="22" cy="22" r="14"/><circle cx="22" cy="22" r="8"/><path d="M22 17v5l3 2"/></svg></div>
  <div class="b-item abs" style="left:882px;top:308px"><h4>24/7 uptime</h4><p>Lorem ipsum dolor sit amet,<br>labore et dolore magna aliqua.</p></div>

  <div class="b-icon abs" style="left:556px;top:493px"><svg width="44" height="44" viewBox="0 0 44 44" fill="none" stroke="#fff" stroke-width="2"><path d="M8 34l10-10 6 6 12-14"/><path d="M28 16h8v8"/></svg></div>
  <div class="b-item abs" style="left:300px;top:592px;width:600px;text-align:center"><h4 style="font-size:16px">Throughput increases (30–50% faster)</h4><p>Lorem ipsum dolor sit amet,<br>labore et dolore magna aliqua.</p></div>
</section>

<section class="quote-banner abs" role="img" aria-label="Tammo cooking robots lined up on a kitchen line">
  <h2 class="heading abs" style="left:0">Tammo helped us reduce cooking<br>times by 40%.</h2>
  <a class="btn abs"><span>Book a Demo</span></a>
</section>

<h2 class="section-title heading abs audience-title">Who<span class="tag"><span>It’s For</span></span></h2>
<div class="aud abs" style="left:112px;top:2628px"><div class="photo" role="img" aria-label="Long restaurant table set with plated dishes" style="background:linear-gradient(160deg,#c9ccc9,#7c7f7c 60%,#4a4c4b)"></div><h5>QSR Restaurants</h5></div>
<div class="aud abs" style="left:360px;top:2628px"><div class="photo" role="img" aria-label="Burger, fries and a soft drink on a red tray" style="background:linear-gradient(160deg,#6b4a2f,#c1782f 50%,#c4262a)"></div><h5>Fast casual</h5></div>
<div class="aud abs" style="left:606px;top:2628px"><div class="photo" role="img" aria-label="Chef's hat and kitchen utensils on a counter" style="background:linear-gradient(160deg,#e4e0da,#b9ad9c 60%,#f2f0ec)"></div><h5>Catering/commissaries</h5></div>
<div class="aud abs" style="left:855px;top:2628px"><div class="photo" role="img" aria-label="Carved pumpkins lit on a dark porch" style="background:linear-gradient(160deg,#1f2030,#5a3320 55%,#e07a22)"></div><h5>Ghost kitchens</h5></div>

<section class="testimonials abs">
  <h2 class="section-title heading abs">CLIENT<span class="tag"><span>TESTIMONIALS</span></span></h2>
  <article class="t-card abs" style="left:108px">
    <span class="quote-mark">“</span>
    <div class="t-head"><div class="avatar" role="img" aria-label="Customer portrait"></div><div><div class="t-name">Marta Velinska</div><div class="t-place"><i></i>Russia</div></div></div>
    <p>Lorem ipsum dolor sit amet, consectetur adipiscing elit, sed eiusmod incididunt ut labore et dolore....</p>
  </article>
  <article class="t-card abs" style="left:444px">
    <span class="quote-mark">“</span>
    <div class="t-head"><div class="avatar" role="img" aria-label="Customer portrait"></div><div><div class="t-name">Oskar Penfield</div><div class="t-place"><i></i>United Kingdom</div></div></div>
    <p>Lorem ipsum dolor sit amet, consectetur adipiscing elit, sed eiusmod incididunt ut labore et dolore....</p>
  </article>
  <article class="t-card abs" style="left:781px">
    <span class="quote-mark">“</span>
    <div class="t-head"><div class="avatar" role="img" aria-label="Customer portrait"></div><div><div class="t-name">Lena H</div><div class="t-place"><i></i>Switzerland</div></div></div>
    <p>Lorem ipsum dolor sit amet, consectetur adipiscing elit, sed eiusmod incididunt ut labore et dolore....</p>
  </article>
</section>

<h2 class="video-title heading abs">Watch Tammo cook a full batch from<br><span class="tag"><span>start to finish.</span></span></h2>
<div class="video abs" role="img" aria-label="Video of Tammo cooking at a trade show booth"></div>
<div class="play abs"><svg width="18" height="20" viewBox="0 0 18 20"><path d="M2 1l15 9-15 9z" fill="#111"/></svg></div>

<footer class="site-footer abs">
  <div class="f-col abs" style="left:97px;top:64px">
    <h6>Quick Links</h6>
    <ul>
      <li>➔ Home</li><li>➔ About Us</li><li>➔ Menu</li><li>➔ Order Online</li><li>➔ What’s New</li><li>➔ Contact Us</li>
    </ul>
  </div>
  <div class="f-col abs" style="left:297px;top:64px">
    <h6>Other Links</h6>
    <ul>
      <li>➔ FAQ</li><li>➔ Terms of Use</li><li>➔ Privacy Policy</li><li>➔ Support Links</li><li>➔ Conditions</li>
    </ul>
  </div>
  <div class="f-col abs" style="left:507px;top:64px">
    <h6>Contact Us</h6>
    <div class="f-contact"><span class="ic"><svg width="14" height="16" viewBox="0 0 14 16"><path d="M7 1a5 5 0 0 1 5 5c0 4-5 9-5 9S2 10 2 6a5 5 0 0 1 5-5z" fill="#fff"/><circle cx="7" cy="6" r="2" fill="var(--red)"/></svg></span>Company Name,United State.</div>
    <div class="f-contact"><span class="ic"><svg width="16" height="12" viewBox="0 0 16 12"><rect width="16" height="12" rx="2" fill="#fff"/><path d="M1 1l7 6 7-6" stroke="var(--red)" fill="none" stroke-width="1.5"/></svg></span>info@companyname.in</div>
    <div class="f-contact"><span class="ic"><svg width="14" height="14" viewBox="0 0 14 14"><path d="M3 1l3 3-2 2a8 8 0 0 0 4 4l2-2 3 3-2 2C6 13 1 8 1 3z" fill="#fff"/></svg></span>+1888 8888 8888</div>
  </div>
  <div class="f-col news abs" style="left:828px;top:64px">
    <h6>Sign Up to Our Newsletter</h6>
    <p>Lorem ipsum dolor sit amet,consectetur<br>adipiscing elit,adipiscing elit.</p>
    <div class="field">Email</div>
    <div class="subscribe">Subscribe</div>
  </div>
  <div class="f-rule abs"></div>
  <div class="copyright abs">Copyrights@2025.Company Name.All Rights Reserved</div>
</footer>

</body>
</html>
```